Deodorant Product Sales One Pager and Annexes

Schedule: Very short deadline - to be complete within 12 hours
Budget: 2-3 hours
Format: Adobe Illustrator / A4 landscape or portrait - for submission by email in PDF
OBJECTIVE
We need a one pager sales sheet and its annexes to present a new deodorant range to the largest supermarket chain in Australia. This is a very important submission that can create more design projects for you. Please refer to the attachments for a starting point. We need to keep the design minimalist and elegant, stylish, clean and chic IN KEEPING WITH THE 1.618 ratio. Styles to avoid are too bright colors, clutter, comic or gimmicky styles. Please maintain a sense of high quality design and professionalism as this is a premium product in Australia.
TARGET AUDIENCE
Senior buyer of largest supermarket chain in Australia
Attachments:
Product one pager
Annexes to one pager
Product shots in low and high resolution
Target Market(s)
Senior cosmetics buyer at Australia's largest supermarket chain
Industry/Entity Type
Landscape

```html
<!DOCTYPE html>
<html lang="en">
<head>
<meta charset="utf-8">
<title>The Magnesium Trend</title>
<link rel="stylesheet" href="https://fonts.googleapis.com/css2?family=Bitter:ital,wght@1,400;1,700&family=Roboto:wght@400;700&family=Montserrat:wght@700&display=swap">
<style>
  :root {
    --page: #ffffff;
    --ink: #4c5a68;
    --ink-strong: #3b4754;
    --brand: #5d6c79;
    --chart-line: #1f5fe0;
    --chart-grid: #e6e9ee;
    --chart-text: #8a939c;
    --chart-axis: #6f8fc4;
    --chart-border: #d6d9de;
  }
  * { margin: 0; padding: 0; box-sizing: border-box; }
  html, body { width: 1200px; height: 851px; overflow: hidden; background: var(--page); }
  .sheet { position: relative; width: 1200px; height: 851px; }
  .trend { position: absolute; left: 328px; top: 180px; width: 546px; color: var(--ink); font-family: "Bitter", Georgia, serif; font-style: italic; }
  .trend-title { font-weight: 700; font-size: 18px; color: var(--ink-strong); letter-spacing: .1px; }
  .trend-quote { margin-top: 23px; font-size: 14.6px; line-height: 21.2px; text-align: justify; }
  .trend-chart { display: block; margin-top: 22px; margin-left: 3px; }
  .trend-caption { margin-top: 28px; font-size: 15px; font-weight: 700; }
  .brand { position: absolute; left: 995px; top: 736px; font-family: "Montserrat", Arial, sans-serif; font-weight: 700; font-size: 29px; color: var(--brand); letter-spacing: -.5px; display: flex; align-items: flex-end; gap: 3px; }
  .brand-dot { width: 7px; height: 7px; border-radius: 50%; border: 1px solid var(--brand); margin-bottom: 6px; }
  .chart-small { font-family: "Roboto", Arial, sans-serif; }
</style>
</head>
<body>
<main class="sheet">
  <section class="trend">
    <h1 class="trend-title">The Magnesium Trend</h1>
    <p class="trend-quote">‘Growing consumer awareness of their own deficiencies, its health benefits, and the emergence of innovative forms are making magnesium the hottest ingredient in the mineral category. With between 70 and 80% of the population not meeting their recommended intakes of magnesium, consumers – and the health care professionals who advise them – are waking up to the importance of the mineral.’ (Nutri Review Weekly, January 2013)</p>

    <svg class="trend-chart" width="524" height="245" viewBox="0 0 524 245" role="img" aria-label="Line chart of web search interest for magnesium deficiency, Australia, July 2007 to May 2013">
      <g class="chart-small" font-size="6.5" fill="var(--chart-text)">
        <text x="6" y="15">Web Search Interest: <tspan font-weight="700" fill="#555">magnesium deficiency</tspan>. Australia, Jul 2007 - May 2013</text>
        <rect x="350" y="7" width="8" height="8" fill="#e88aa8"/>
        <rect x="475" y="3" width="45" height="20" rx="2" fill="#f4f5f7" stroke="var(--chart-border)"/>
        <circle cx="491" cy="13" r="3.5" fill="none" stroke="#666" stroke-width="2"/>
        <path d="M506 12 l3 3 3-3z" fill="#666"/>
        <text x="6" y="56" font-size="7.5" font-weight="700" fill="#333">Interest over time</text>
        <circle cx="90" cy="53" r="3.5" fill="none" stroke="#bbb" stroke-width=".7"/>
        <text x="6" y="67" font-size="5.5" fill="#555">The number 100 represents the peak search interest</text>
        <rect x="388" y="62" width="6" height="6" fill="#fff" stroke="#bbb" stroke-width=".7"/>
        <text x="398" y="67" font-size="5.5" fill="#555">News headlines</text>
        <text x="474" y="67" font-size="5.5">Forecast</text>
        <circle cx="512" cy="65" r="3" fill="none" stroke="#bbb" stroke-width=".7"/>
        <line x1="6" y1="72" x2="522" y2="72" stroke="var(--chart-border)" stroke-width=".7"/>
      </g>
      <g stroke="var(--chart-grid)" stroke-width=".8">
        <line x1="8" y1="104" x2="522" y2="104"/>
        <line x1="8" y1="135.75" x2="522" y2="135.75"/>
        <line x1="8" y1="167.5" x2="522" y2="167.5"/>
        <line x1="8" y1="199.25" x2="522" y2="199.25"/>
        <line x1="8" y1="231" x2="522" y2="231"/>
      </g>
      <g class="chart-small" font-size="5" fill="var(--chart-text)">
        <text x="9" y="102">100</text>
        <text x="9" y="134">75</text>
        <text x="9" y="165">50</text>
        <text x="9" y="197">25</text>
      </g>
      <polyline fill="none" stroke="var(--chart-line)" stroke-width="1.2" stroke-linejoin="round"
        points="8,231 15.6,203.1 23.1,208.1 30.7,199.3 38.2,195.4 45.8,192.9 53.4,199.3 60.9,208.1 68.5,195.4 76,199.3 83.6,208.1 91.1,205.6 98.7,199.3 106.3,203.1 113.8,192.9 121.4,205.6 128.9,201.8 136.5,208.1 144.1,198 151.6,199.3 159.2,196.7 166.7,190.4 174.3,182.7 181.9,186.6 189.4,180.2 197,177.7 204.5,173.9 212.1,192.9 219.7,148.5 227.2,154.8 234.8,139.6 242.3,152.3 249.9,154.8 257.4,129.4 265,148.5 272.6,152.3 280.1,152.3 287.7,154.8 295.2,144.6 302.8,148.5 310.4,161.2 317.9,144.6 325.5,161.2 333,165 340.6,173.9 348.2,177.7 355.7,170 363.3,173.9 370.8,167.5 378.4,161.2 386,157.3 393.5,177.7 401.1,180.2 408.6,173.9 416.2,167.5 423.8,173.9 431.3,177.7 438.9,167.5 446.4,180.2 454,182.7 461.6,167.5 469.1,165 476.7,182.7 484.2,186.6 491.8,167.5 499.3,148.5 506.9,170 514.5,177.7 522,161.2"/>
      <g class="chart-small" font-size="5.5">
        <text x="294" y="226" fill="#333" text-anchor="middle">Note</text>
        <g fill="var(--chart-axis)" font-size="5" text-anchor="middle">
          <text x="38" y="241">Jul 2008</text>
          <text x="129" y="241">Jul 2009</text>
          <text x="220" y="241">Jul 2010</text>
          <text x="310" y="241">Jul 2011</text>
          <text x="401" y="241">Jul 2012</text>
          <text x="491" y="241">Jul 2013</text>
        </g>
      </g>
    </svg>

    <p class="trend-caption">Web search interest for magnesium deficiency increases by 200%</p>
  </section>

  <div class="brand">velora<span class="brand-dot"></span></div>
</main>
</body>
</html>
```